Business Card Design

New business card design

Target Market(s)

Residential & Commercial Property Managers

Industry/Entity Type

Plumbing Services

Contact Information for Business Card

Name - Rowan Keddle, title - Director, Phone Number - 0431 286 517, email - rowan@tbk-plumbing.com.au, Company ABN - 73 215 904 386,

Font styles to use
Sans Serif

Colors
0054AA
0677BA
7BADD7
CADEEF
E8F1F8

```html
<!DOCTYPE html>
<html lang="en">
<head>
<meta charset="utf-8">
<title>TBK Plumbing Services – Business Card</title>
<link href="https://fonts.googleapis.com/css2?family=Montserrat:wght@400;500;700&display=swap" rel="stylesheet">
<style>
  :root {
    --backdrop: #cfd5d5;
    --card: #f3f3f1;
    --ink: #16191c;
    --muted: #3a3d40;
    --accent: #22a4de;
    --accent-deep: #0677ba;
  }
  * { margin: 0; padding: 0; box-sizing: border-box; }
  html, body { width: 1200px; height: 881px; overflow: hidden; }
  body {
    background: var(--backdrop);
    font-family: "Montserrat", sans-serif;
    color: var(--ink);
    position: relative;
  }
  .card {
    position: absolute;
    top: 282px;
    width: 520px;
    height: 318px;
    background: var(--card);
    box-shadow: 0 10px 30px rgba(0,0,0,.12);
  }
  .card--front { left: 50px; border-bottom: 3px solid var(--accent); }
  .card--back { left: 630px; }

  .brand {
    position: absolute;
    display: flex;
    align-items: center;
    gap: 12px;
    font-weight: 400;
    color: var(--ink);
    white-space: nowrap;
  }
  .brand__dot {
    width: 18px; height: 18px;
    border-radius: 50%;
    background: var(--accent);
    flex: none;
  }
  .card--front .brand { top: 54px; left: 150px; font-size: 26px; letter-spacing: 2px; }
  .card--back .brand { top: 50%; left: 50%; transform: translate(-50%, -50%); font-size: 30px; letter-spacing: 2px; }

  .person {
    position: absolute;
    top: 158px;
    right: 300px;
    text-align: right;
  }
  .person__name { font-size: 21px; font-weight: 700; color: var(--accent); }
  .person__role { font-size: 15px; color: var(--muted); margin-top: 4px; }

  .divider {
    position: absolute;
    top: 160px;
    left: 232px;
    width: 2px;
    height: 50px;
    background: var(--accent);
  }

  .contact {
    position: absolute;
    top: 162px;
    left: 248px;
    list-style: none;
    font-size: 14px;
    color: var(--muted);
  }
  .contact__item { display: flex; align-items: center; gap: 7px; margin-bottom: 8px; }
  .contact__icon { width: 13px; height: 13px; flex: none; }

  .abn {
    position: absolute;
    top: 240px;
    left: 0;
    width: 100%;
    text-align: center;
    font-size: 14px;
    color: var(--muted);
  }
</style>
</head>
<body>
  <section class="card card--front" aria-label="Business card front">
    <div class="brand"><span class="brand__dot"></span>tbk plumbing services</div>

    <div class="person">
      <p class="person__name">Rowan Keddle</p>
      <p class="person__role">Director</p>
    </div>

    <div class="divider"></div>

    <ul class="contact">
      <li class="contact__item">
        <svg class="contact__icon" viewBox="0 0 24 24" aria-hidden="true">
          <path fill="var(--accent)" d="M6.6 10.8a15.1 15.1 0 0 0 6.6 6.6l2.2-2.2a1 1 0 0 1 1-.25 11.4 11.4 0 0 0 3.6.57 1 1 0 0 1 1 1V20a1 1 0 0 1-1 1A17 17 0 0 1 3 4a1 1 0 0 1 1-1h3.5a1 1 0 0 1 1 1c0 1.25.2 2.45.57 3.57a1 1 0 0 1-.25 1z"/>
        </svg>
        0431 286 517
      </li>
      <li class="contact__item">
        <svg class="contact__icon" viewBox="0 0 24 24" aria-hidden="true">
          <rect x="2" y="5" width="20" height="14" rx="2" fill="var(--accent)"/>
          <path d="M3 6l9 7 9-7" fill="none" stroke="#fff" stroke-width="1.8"/>
        </svg>
        rowan@tbk-plumbing.com.au
      </li>
    </ul>

    <p class="abn">Company ABN - 73 215 904 386</p>
  </section>

  <section class="card card--back" aria-label="Business card back">
    <div class="brand"><span class="brand__dot"></span>tbk plumbing services</div>
  </section>
</body>
</html>
```